Online Shop Maren

We need a web design for an online shop, called "Lirvo Dune Jewels". The shop should have an extraordinary, elegant look, as shown in the Quellwick Advertising Picture in our Briefing.pdf (attached). Please have a look at our Briefing regarding website colours, background ideas, and elements to be included. The online shop is about professional jewellery design pieces, where each piece is handmade of high quality materials, also unique pieces and unique editions possible. It should attract extraordinary people and visualize that its a very individual and unique design jewellery. You can get an idea of whom it should attract by reading our target group. Colours to be used are jewellery-Velvet red, Black / anthracite, exclusive colours, silverish-white, bronze-brown and golden.

Please play around when designing with the image pictures we attach, preferably more vertical pictures, no panoramic pictures like in Brovenka Shop. Also include the BLACK logo of lirvo dune. We include the SITEMAP in the briefing and also another folder with product pictures you can use for the draft.

Regarding Functions, the store will have the SAME (technical) functions as this page:http://www.brovenka-shop.eu/ - using the "most famous" products/categories for the starting page, going into individual product pages by clicking these images and then leading to a detailed page for one product only.

Target Market(s)

Jewellery-lovers, who appreciate extraordinary things, creative economy/fashion-industries, stylists, Style consultants, outfitter, theatres, operas, production sites, Cocktail-, Dinner and Bridefashion, exclusive traditional costume stores, dancesports and tango argento dancers

Industry/Entity Type

Shop

Requirements
Must have
• Must include:
• Colours as per briefing
• Background ideas/images as per briefing/pictures sent
• Sitemap as per briefing
• Social buttons
• Logo
• Design for 3 pages: Starting page showing big images, attractive design and the 4 popular categories
• Subpage with different products of one category (i.e. bracelets)
• Detail page with one individual product only
Should not have
• no fresh, playful colours like yellow, orange, green, blue
• no cheap design, no panorama pictures

```html
<!DOCTYPE html>
<html lang="en">
<head>
<meta charset="utf-8">
<title>Lirvo Dune Jewels</title>
<link href="https://fonts.googleapis.com/css2?family=Cinzel:wght@400;700&family=Pinyon+Script&family=Ubuntu:wght@400;500&family=Oswald:wght@500;700&display=swap" rel="stylesheet">
<style>
:root{
  --gold:#a98b50;
  --gold-light:#c8a96a;
  --cream:#e6d9b8;
  --ink:#050505;
  --text:#9a9a9a;
  --text-light:#cfcfcf;
  --offer:#a48a45;
  --line:#2a2a2a;
}
*{margin:0;padding:0;box-sizing:border-box}
html,body{width:1112px;height:1200px;overflow:hidden;background:var(--ink)}
body{position:relative;font-family:"Ubuntu",sans-serif;color:var(--text)}
.abs{position:absolute}

.hero{left:0;top:0;width:1112px;height:655px;
  background:
    radial-gradient(ellipse 300px 260px at 330px 230px,rgba(60,60,60,.45),rgba(0,0,0,0) 70%),
    radial-gradient(ellipse 220px 300px at 120px 180px,rgba(45,45,45,.5),rgba(0,0,0,0) 70%),
    linear-gradient(180deg,#141414 0%,#222 45%,#1b1b1b 100%)}
.hero-photo{left:700px;top:60px;width:412px;height:595px;
  background:
    radial-gradient(ellipse 48px 62px at 210px 135px,#b5b5b5 0%,#7a7a7a 45%,rgba(60,60,60,0) 100%),
    radial-gradient(ellipse 90px 40px at 200px 280px,rgba(200,200,200,.55),rgba(120,120,120,0) 80%),
    radial-gradient(ellipse 40px 90px at 330px 350px,rgba(150,150,150,.55),rgba(80,80,80,0) 80%),
    radial-gradient(ellipse 170px 260px at 240px 380px,#2e2e2e 0%,#1a1a1a 60%,rgba(20,20,20,0) 100%),
    radial-gradient(ellipse 110px 150px at 230px 110px,rgba(40,40,40,.9),rgba(30,30,30,0) 100%)}
.topbar{left:0;top:0;width:1112px;height:58px;background:linear-gradient(#080808,rgba(8,8,8,0))}
.account{top:33px;left:602px;font-size:10px;color:var(--gold-light);display:flex;gap:20px;align-items:center}
.account .sep{color:var(--text)}
.cart{display:flex;align-items:center;gap:5px}
.logo{left:168px;top:56px;color:var(--cream)}
.logo .name{font-size:33px;line-height:1}
.logo .sub{font-size:18px;margin:8px 0 0 48px;display:flex;align-items:center;gap:8px;color:#e8e2d4}
.logo .dot{width:5px;height:5px;background:#e8e2d4;transform:rotate(45deg);display:block}
.nav{top:76px;left:404px;display:flex;font-size:10.5px;font-weight:500;color:var(--gold-light)}
.nav span{display:inline-block}
.title{left:185px;top:234px;font-family:"Cinzel",serif;font-weight:400;font-size:47px;color:var(--gold);letter-spacing:1px;white-space:nowrap}
.tagline{left:252px;top:290px;font-family:"Pinyon Script",cursive;font-size:40px;color:var(--gold);white-space:nowrap}
.rule{left:182px;width:491px;height:3px;border-top:1px solid var(--gold);border-bottom:1px solid #6a5530}
.intro{left:182px;top:390px;width:491px;text-align:center;font-size:10px;line-height:21px;color:var(--text)}
.order{left:319px;top:490px;width:192px;height:44px;border-radius:22px;background:linear-gradient(#f2f2f2,#b9b9b9);font-family:"Cinzel",serif;font-size:20px;color:#4a4a4a;text-align:center;line-height:44px}
.slide-arrow{top:330px}

.lower{left:0;top:655px;width:1112px;height:470px;
  background:
    radial-gradient(ellipse 260px 160px at 120px 330px,rgba(40,40,40,.55),rgba(0,0,0,0) 70%),
    radial-gradient(ellipse 240px 170px at 1000px 300px,rgba(38,38,38,.5),rgba(0,0,0,0) 70%),
    #050505}

.banner{top:676px;width:381px;height:129px;overflow:hidden}
.banner.store{left:168px;background:#0d1020}
.store-photo{left:0;top:0;width:381px;height:129px;
  background:
    radial-gradient(ellipse 60px 80px at 290px 95px,#c23a3c 0%,rgba(170,50,55,.6) 60%,rgba(0,0,0,0) 100%),
    radial-gradient(ellipse 40px 35px at 300px 28px,#8a5a48 0%,rgba(90,60,50,0) 100%),
    linear-gradient(90deg,#0d1020 0%,#11142a 45%,#4b4650 62%,#7f7660 78%,#5a5560 100%)}
.store-script{left:22px;top:6px;font-family:"Pinyon Script",cursive;font-size:36px;color:#fff}
.store-shop{left:115px;top:22px;font-size:17px;color:var(--cream)}
.store-name{left:18px;top:44px;font-size:26px;color:var(--cream)}
.store-text{left:18px;top:84px;width:240px;font-size:12px;line-height:17px;color:#fff}
.banner.offer{left:565px;background:var(--offer)}
.offer-photo{left:0;top:0;width:381px;height:129px;
  background:
    radial-gradient(ellipse 45px 70px at 262px 95px,#f2f2f2 0%,rgba(230,230,230,.7) 50%,rgba(0,0,0,0) 100%),
    radial-gradient(ellipse 25px 30px at 262px 30px,#6a5040 0%,rgba(80,60,50,0) 100%),
    linear-gradient(90deg,var(--offer) 0%,#a48a45 52%,#8a7a5a 62%,#9aa0a8 80%,#5a6478 100%)}
.offer-1{left:27px;top:30px;font-family:"Oswald",sans-serif;font-weight:500;font-size:17px;color:#111}
.offer-2{left:49px;top:50px;font-family:"Oswald",sans-serif;font-weight:700;font-size:28px;color:#fff}
.offer-3{left:35px;top:88px;font-family:"Oswald",sans-serif;font-weight:500;font-size:16px;color:#111}

.section-title{top:828px;font-size:22px;font-weight:400;color:var(--gold-light)}
.welcome-photo{left:168px;top:869px;width:220px;height:118px;
  background:
    radial-gradient(ellipse 60px 40px at 110px 45px,#c49a88 0%,rgba(180,140,130,0) 100%),
    radial-gradient(ellipse 50px 12px at 120px 95px,rgba(245,240,230,.8),rgba(240,235,225,0) 100%),
    linear-gradient(110deg,#3a2538 0%,#6a3f5c 35%,#a07a80 60%,#dcd6d6 85%,#ecebea 100%)}
.welcome-text{left:168px;top:998px;width:222px;font-size:8.5px;line-height:16px;color:var(--text-light)}
.carousel{left:922px;top:842px}

.product{top:872px;width:161px}
.product .thumb{width:161px;height:118px;border:2px solid #3a3a3a}
.thumb.black{background:radial-gradient(ellipse 70px 25px at 80px 60px,#0c0c0c 0%,#1a1a1a 70%,rgba(0,0,0,0) 100%),radial-gradient(ellipse at 50% 25%,#6a6a6a,#303030 60%,#222)}
.thumb.gold{background:radial-gradient(ellipse 60px 45px at 80px 70px,rgba(196,150,60,.55),rgba(0,0,0,0) 100%),linear-gradient(#3a3e46,#2a2e34)}
.thumb.silver{background:radial-gradient(ellipse 70px 45px at 80px 55px,#d8d8d8 0%,#9a9a9a 45%,#555 80%,#3a3a3a 100%)}
.product h3{margin-top:15px;font-family:"Oswald",sans-serif;font-weight:500;font-size:11px;color:var(--gold)}
.product p{margin-top:6px;font-size:8.5px;line-height:16px;color:var(--text-light)}
.product .buy-row{margin-top:8px;display:flex;justify-content:space-between;align-items:center}
.price{font-size:16px;color:var(--gold)}
.buy{width:75px;height:21px;background:linear-gradient(#fff,#c8c8c8);font-size:9.5px;color:#444;text-align:center;line-height:21px}

.footer{left:0;top:1125px;width:1112px;height:75px;background:#0a0a0a;border-top:1px solid var(--line)}
.footer-nav{left:171px;top:21px;display:flex;font-size:7.5px;color:#ccc}
.footer-nav span{display:inline-block}
.footer-nav .sep{color:#ccc}
.copy{left:171px;top:42px;font-size:7.5px;color:#ccc}
.social{left:875px;top:27px;display:flex;gap:5px}
.social span{width:19px;height:19px;border-radius:50%;background:#4a5260;display:block}
</style>
</head>
<body>

<div class="abs hero"></div>
<div class="abs hero-photo" role="img" aria-label="Black and white portrait of a model wearing a diamond necklace and drop earrings"></div>
<div class="abs topbar"></div>

<div class="abs account">
  <span>My Account</span><span class="sep">|</span><span>Login</span><span class="sep">|</span><span>Register</span>
  <span class="cart" style="margin-left:20px">
    <svg width="13" height="11" viewBox="0 0 13 11"><path d="M0 1h2l2 6h7l1.5-4.5H3" fill="none" stroke="#c8a96a" stroke-width="1.2"/><circle cx="5" cy="9.5" r="1" fill="#c8a96a"/><circle cx="10" cy="9.5" r="1" fill="#c8a96a"/></svg>
    Your cart is : 0 items</span>
</div>

<div class="abs logo"><div class="name">Lirvo Dune</div><div class="sub"><i class="dot"></i>Jewels<i class="dot"></i></div></div>

<nav class="abs nav">
  <span style="width:78px">HOME</span><span style="width:108px">ONLINE SHOP</span><span style="width:118px">INFO &amp; FACTS</span><span style="width:93px">PARTNER</span><span style="width:100px">ABOUT ME</span><span>CONTACT</span>
</nav>

<svg class="abs slide-arrow" style="left:56px" width="60" height="60" viewBox="0 0 60 60"><circle cx="30" cy="30" r="28" fill="none" stroke="#3a3a3a" stroke-width="2"/><path d="M40 16 L14 30 L40 44 L32 30 Z" fill="#3a3a3a"/></svg>
<svg class="abs slide-arrow" style="left:994px" width="60" height="60" viewBox="0 0 60 60"><circle cx="30" cy="30" r="28" fill="none" stroke="#2e2e2e" stroke-width="2"/><path d="M20 16 L46 30 L20 44 L28 30 Z" fill="#2e2e2e"/></svg>

<h1 class="abs title">Lirvo Dune Jewels</h1>
<div class="abs tagline">that's inherently Human</div>
<div class="abs rule" style="top:374px"></div>
<p class="abs intro">It is a long established fact that a reader will be distracted by the readable content of a page when looking at its layout. The point of using Lorem Ipsum is that it has a more-or-less normal distribution of letters, as opposed to using 'Content here, content here...</p>
<div class="abs rule" style="top:463px"></div>
<div class="abs order">Order now</div>

<div class="abs lower"></div>

<div class="abs banner store">
  <div class="abs store-photo" role="img" aria-label="Model in a red dress wearing earrings"></div>
  <div class="abs store-script">Store</div>
  <div class="abs store-shop">Shop Online</div>
  <div class="abs store-name">Lirvo Dune</div>
  <div class="abs store-text">It is a long established fact that a reader will be distracted by the readable...</div>
</div>

<div class="abs banner offer">
  <div class="abs offer-photo" role="img" aria-label="Model in a white jacket wearing a pearl necklace"></div>
  <div class="abs offer-1">LOREM IPSUM IS</div>
  <div class="abs offer-2">10% OFFER</div>
  <div class="abs offer-3">FOR SPECIAL PRODUCTS</div>
</div>

<h2 class="abs section-title" style="left:168px">Welcome to Lirvo Dune</h2>
<h2 class="abs section-title" style="left:422px">Our Products</h2>
<svg class="abs carousel" width="22" height="10" viewBox="0 0 22 10"><path d="M6 1 L2 5 L6 9" fill="none" stroke="#bbb" stroke-width="1.2"/><path d="M16 1 L20 5 L16 9" fill="none" stroke="#bbb" stroke-width="1.2"/></svg>

<div class="abs welcome-photo" role="img" aria-label="Model wearing a pearl necklace and bracelet"></div>
<p class="abs welcome-text">It is a long established fact that a reader will be distracted by the readable content of a page when looking at its layout. The point of using Lorem Ipsum is that it has a more-or-less normal distribution of letters, as opposed to using 'Content here, content here...</p>

<div class="abs product" style="left:424px">
  <div class="thumb black" role="img" aria-label="Black beaded collar necklace"></div>
  <h3>FINE JEWEL EDITION</h3>
  <p>It is a long established fact that a reader will be distracted by the readable...</p>
  <div class="buy-row"><span class="price">275 €</span><span class="buy">Buy Now</span></div>
</div>
<div class="abs product" style="left:605px">
  <div class="thumb gold" role="img" aria-label="Gold and crystal drop necklace"></div>
  <h3>FINE JEWEL EDITION</h3>
  <p>It is a long established fact that a reader will be distracted by the readable...</p>
  <div class="buy-row"><span class="price">275 €</span><span class="buy">Buy Now</span></div>
</div>
<div class="abs product" style="left:786px">
  <div class="thumb silver" role="img" aria-label="Silver beaded collar necklace"></div>
  <h3>FINE JEWEL EDITION</h3>
  <p>It is a long established fact that a reader will be distracted by the readable...</p>
  <div class="buy-row"><span class="price">275 €</span><span class="buy">Buy Now</span></div>
</div>

<footer class="abs footer">
  <div class="abs footer-nav">
    <span style="width:37px">HOME</span><span class="sep" style="width:15px">|</span><span style="width:63px">ONLINE SHOP</span><span class="sep" style="width:15px">|</span><span style="width:63px">INFO &amp; FACTS</span><span class="sep" style="width:15px">|</span><span style="width:44px">PARTNER</span><span class="sep" style="width:15px">|</span><span style="width:52px">ABOUT ME</span><span class="sep" style="width:15px">|</span><span>CONTACT</span>
  </div>
  <div class="abs copy">COPYRIGHTS 2013. LIRVO DUNE. ALL RIGHTS RESERVED.</div>
  <div class="abs social"><span aria-label="Social link"></span><span aria-label="Social link"></span><span aria-label="Social link"></span></div>
</footer>

</body>
</html>
```